Business card design for Automotive workshop

We need a business card for a new automotive repair and tyre shop called Keelstone Prime Automotive located in New Zealand. We are a clean, modern and fresh workshop and company.

Front needs to feature logo,
my name:
Marlo Fenwicke (director)

Address:
48 Tarn Lane
Whitianga 3510

Phone: 07 594 2713
Mobile: 027 451 9362
Email: office@keelstoneautomotive.example.nz
Website: keelstoneautomotive.example.nz

Back needs to feature an area to write down appointment details, date and time.

Also feature a list of jobs and work we do such as,
Vehicle Servicing
All Mechanical Repairs
Warrant of Fitness
Tyres & Wheel Alignments
Automotive Diagnostics
Automotive Parts & Supplies

```html
<!DOCTYPE html>
<html lang="en">
<head>
<meta charset="utf-8">
<title>Keelstone Prime Automotive – Business Card</title>
<link href="https://fonts.googleapis.com/css2?family=Poppins:wght@400;500;600;700&family=Exo+2:ital,wght@1,800&display=swap" rel="stylesheet">
<style>
  :root{
    --stage:#6b717b;
    --ink:#1d1e20;
    --black:#050505;
    --red:#e3151f;
    --white:#ffffff;
    --dots:#3a3a3a;
  }
  *{box-sizing:border-box;margin:0;padding:0}
  html,body{width:1200px;height:900px;overflow:hidden}
  body{
    background:linear-gradient(90deg,#4a515c 0%,#7c828b 100%);
    font-family:'Poppins',sans-serif;
    position:relative;
  }
  .card{
    position:absolute;left:280px;width:640px;height:366px;overflow:hidden;
    box-shadow:0 14px 30px rgba(0,0,0,.35);
  }
  /* ---------- back ---------- */
  .card-back{top:62px;background:var(--ink);color:var(--white)}
  .brand{display:flex;align-items:center;gap:10px;color:var(--red);font-weight:700;letter-spacing:.5px}
  .card-back .brand{position:absolute;top:38px;left:0;right:0;justify-content:center;font-size:28px}
  .brand-mark{width:16px;height:16px;background:var(--red);flex:none}
  .services{position:absolute;top:100px;left:0;right:0;text-align:center}
  .services-title{color:var(--red);font-weight:700;font-size:16px;letter-spacing:.5px;margin-bottom:6px}
  .services-line{font-size:13px;font-weight:500;line-height:1.45}
  .services-line .sep{color:var(--red);margin:0 6px}
  .appointment{
    position:absolute;left:22px;right:22px;bottom:22px;height:150px;background:var(--white);
    padding:34px 32px 0;
  }
  .appt-row{display:flex;align-items:flex-end;gap:8px;height:46px;font-size:15px;font-weight:500}
  .appt-label{color:var(--red)}
  .appt-line{flex:1;border-bottom:2px dotted var(--dots);margin-bottom:5px}
  .appt-line.date{flex:1.6}
  /* ---------- front ---------- */
  .card-front{top:472px;background:var(--white)}
  .card-front .brand{position:absolute;top:78px;right:40px;font-size:24px}
  .contact-panel{
    position:absolute;left:0;top:176px;width:440px;height:148px;background:var(--red);
    clip-path:polygon(0 0,300px 0,440px 100%,0 100%);color:var(--white);
    padding:18px 0 0 34px;
  }
  .person-name{font-family:'Exo 2',sans-serif;font-style:italic;font-weight:800;font-size:22px;letter-spacing:.5px;line-height:1}
  .person-role{font-family:'Exo 2',sans-serif;font-style:italic;font-weight:800;font-size:13px;margin:3px 0 10px}
  .contact-list{list-style:none;font-size:13px;line-height:1.55}
  .contact-list li{display:flex;align-items:center;gap:7px}
  .contact-list svg{width:12px;height:12px;fill:var(--white);flex:none}
  .contact-list .gap{width:10px}
  .address-band{
    position:absolute;left:0;right:0;bottom:0;height:36px;background:var(--black);
    border-top:4px solid var(--white);color:var(--white);
    display:flex;align-items:center;gap:10px;padding-left:34px;font-size:14px;font-weight:500;
  }
  .address-band svg{width:12px;height:15px;fill:var(--red)}
</style>
</head>
<body>

<section class="card card-back" aria-label="Card back">
  <div class="brand"><span class="brand-mark"></span>Keelstone Prime Automotive</div>
  <div class="services">
    <p class="services-title">VEHICLE SERVICING</p>
    <p class="services-line">All Mechanical Repairs<span class="sep">•</span>Warrant of Fitness<span class="sep">•</span>Tyres &amp; Wheel Alignments</p>
    <p class="services-line">Automotive Diagnostics<span class="sep">•</span>Automotive Parts &amp; Supplies</p>
  </div>
  <div class="appointment">
    <div class="appt-row"><span class="appt-label">Date:</span><span class="appt-line date"></span><span class="appt-label">Time:</span><span class="appt-line"></span></div>
    <div class="appt-row"><span class="appt-label">Date:</span><span class="appt-line date"></span><span class="appt-label">Time:</span><span class="appt-line"></span></div>
  </div>
</section>

<section class="card card-front" aria-label="Card front">
  <div class="brand"><span class="brand-mark"></span>Keelstone Prime Automotive</div>
  <div class="contact-panel">
    <p class="person-name">MARLO FENWICKE</p>
    <p class="person-role">DIRECTOR</p>
    <ul class="contact-list">
      <li>
        <svg viewBox="0 0 24 24"><path d="M6.6 10.8a15 15 0 0 0 6.6 6.6l2.2-2.2a1 1 0 0 1 1-.25 11.4 11.4 0 0 0 3.6.57 1 1 0 0 1 1 1V20a1 1 0 0 1-1 1A17 17 0 0 1 3 4a1 1 0 0 1 1-1h3.5a1 1 0 0 1 1 1c0 1.25.2 2.45.57 3.57a1 1 0 0 1-.25 1z"/></svg>
        07 594 2713<span class="gap"></span>
        <svg viewBox="0 0 24 24"><path d="M7 1h10a2 2 0 0 1 2 2v18a2 2 0 0 1-2 2H7a2 2 0 0 1-2-2V3a2 2 0 0 1 2-2zm0 3v14h10V4z"/></svg>
        027 451 9362
      </li>
      <li>
        <svg viewBox="0 0 24 24"><path d="M2 5h20v14H2zm2 2v.5l8 5 8-5V7zm0 2.8V17h16V9.8l-8 5z"/></svg>
        office@keelstoneautomotive.example.nz
      </li>
      <li>
        <svg viewBox="0 0 24 24"><path d="M12 2a10 10 0 1 0 0 20 10 10 0 0 0 0-20zm6.9 6h-3a15 15 0 0 0-1.3-3.9A8 8 0 0 1 18.9 8zM12 4c.8 1.2 1.5 2.5 1.9 4h-3.8c.4-1.5 1.1-2.8 1.9-4zM4.3 14a8 8 0 0 1 0-4h3.4a16 16 0 0 0 0 4zm.8 2h3a15 15 0 0 0 1.3 3.9A8 8 0 0 1 5.1 16zm3-8h-3a8 8 0 0 1 4.3-3.9A15 15 0 0 0 8.1 8zM12 20c-.8-1.2-1.5-2.5-1.9-4h3.8c-.4 1.5-1.1 2.8-1.9 4zm2.3-6H9.7a14 14 0 0 1 0-4h4.6a14 14 0 0 1 0 4zm.3 5.9a15 15 0 0 0 1.3-3.9h3a8 8 0 0 1-4.3 3.9zm1.7-5.9a16 16 0 0 0 0-4h3.4a8 8 0 0 1 0 4z"/></svg>
        www.keelstoneautomotive.example.nz
      </li>
    </ul>
  </div>
  <div class="address-band">
    <svg viewBox="0 0 20 26"><path d="M10 0a10 10 0 0 0-10 10c0 7.5 10 16 10 16s10-8.5 10-16A10 10 0 0 0 10 0zm0 14a4 4 0 1 1 0-8 4 4 0 0 1 0 8z"/></svg>
    48 Tarn Lane, Whitianga 3510
  </div>
</section>

</body>
</html>
```